Engagement party email invitation

I need an invitation designed for my upcoming engagement party. I would like the attached picture to be encircled by gum leaves or some sort of garland of green leaves.

Traditional text typeface eg Sackers Gothic Light or Mrs Eaves.

Thanks
Marnie

Font styles to use
Serif
Script

```html
<!DOCTYPE html>
<html lang="en">
<head>
<meta charset="utf-8">
<title>Engagement Invitation – Marnie &amp; Thomas</title>
<link rel="stylesheet" href="https://fonts.googleapis.com/css2?family=Sorts+Mill+Goudy&display=swap">
<style>
  :root {
    --sky: #eef3f7;
    --haze: #dde6ee;
    --skyline: #c6d4e2;
    --hills: #b8c2bf;
    --hills-dark: #a3ada6;
    --water: #cadcea;
    --water-deep: #b7cee0;
    --gold: #7a4a1c;
    --gold-light: #e9bf80;
    --leaf: #3f7a17;
    --leaf-deep: #2a5a0e;
    --leaf-mid: #5d9e2c;
    --leaf-soft: #8cc85c;
    --leaf-pale: #c5e3ab;
    --band: rgba(255, 255, 255, 0.55);
  }
  * { margin: 0; padding: 0; box-sizing: border-box; }
  html, body {
    width: 1200px;
    height: 617px;
    overflow: hidden;
    background: #ffffff;
  }
  .invitation {
    position: relative;
    width: 1200px;
    height: 617px;
    overflow: hidden;
    font-family: "Sorts Mill Goudy", "Goudy Old Style", Georgia, serif;
  }
  .harbour-scene {
    position: absolute;
    inset: 0;
    background: linear-gradient(180deg,
      var(--sky) 0%,
      var(--haze) 24%,
      var(--skyline) 33%,
      var(--hills) 42%,
      var(--hills-dark) 52%,
      var(--water) 64%,
      var(--water-deep) 82%,
      var(--water) 100%);
  }
  .details-band {
    position: absolute;
    left: 0; right: 0;
    top: 407px;
    height: 135px;
    background: var(--band);
  }
  .garland {
    position: absolute;
    inset: 0;
    width: 1200px;
    height: 617px;
  }
  .invitation__text {
    position: absolute;
    left: 0; right: 0;
    text-align: center;
    line-height: 1;
    white-space: nowrap;
    color: var(--gold);
    text-shadow:
      0 -1px 0 var(--gold-light),
      1px 2px 2px rgba(60, 30, 5, 0.35);
  }
  .hosts {
    top: 54px;
    font-size: 50px;
    letter-spacing: 5px;
  }
  .invite-line {
    top: 123px;
    font-size: 50px;
    letter-spacing: 4px;
  }
  .couple {
    top: 236px;
    font-size: 120px;
    font-weight: 400;
    letter-spacing: 2px;
    color: var(--leaf);
    text-shadow:
      0 -2px 0 var(--leaf-soft),
      2px 3px 3px rgba(20, 45, 5, 0.45),
      0 0 8px rgba(255, 255, 255, 0.6);
  }
  .event-date {
    top: 414px;
    font-size: 50px;
    letter-spacing: 4px;
  }
  .event-address {
    top: 483px;
    font-size: 50px;
    letter-spacing: 5px;
  }
</style>
</head>
<body>
  <main class="invitation">
    <div class="harbour-scene" role="img" aria-label="Soft watercolour view of a harbour with a city skyline, wooded hills and moored sailing boats"></div>
    <div class="details-band"></div>

    <svg class="garland" viewBox="0 0 1200 617" role="img" aria-label="Garland of gum leaves, ferns, berries and small blue flowers framing the harbour view">
      <defs>
        <radialGradient id="garland-corner" cx="0.85" cy="0.2" r="0.8">
          <stop offset="0" stop-color="var(--leaf-mid)"/>
          <stop offset="0.45" stop-color="var(--leaf-soft)" stop-opacity="0.9"/>
          <stop offset="1" stop-color="var(--leaf-pale)" stop-opacity="0.35"/>
        </radialGradient>
        <radialGradient id="garland-side" cx="0.7" cy="0.5" r="0.7">
          <stop offset="0" stop-color="var(--leaf-mid)" stop-opacity="0.9"/>
          <stop offset="1" stop-color="var(--leaf-pale)" stop-opacity="0.3"/>
        </radialGradient>
        <radialGradient id="garland-cluster" cx="0.4" cy="0.5" r="0.7">
          <stop offset="0" stop-color="var(--leaf-soft)" stop-opacity="0.85"/>
          <stop offset="1" stop-color="var(--leaf-pale)" stop-opacity="0.3"/>
        </radialGradient>
        <linearGradient id="garland-base" x1="0" y1="1" x2="0.4" y2="0">
          <stop offset="0" stop-color="var(--leaf-deep)" stop-opacity="0.85"/>
          <stop offset="0.45" stop-color="var(--leaf-mid)" stop-opacity="0.7"/>
          <stop offset="1" stop-color="var(--leaf-pale)" stop-opacity="0.3"/>
        </linearGradient>
      </defs>
      <path class="garland__corner" fill="url(#garland-corner)"
        d="M700 0 H1200 V300 C1170 280 1140 240 1100 215 C1060 190 1050 150 1000 140 C960 132 930 100 950 70 C900 60 840 40 780 30 C740 24 710 14 700 0 Z"/>
      <path class="garland__side" fill="url(#garland-side)"
        d="M1200 225 C1160 240 1120 270 1115 310 C1110 350 1125 380 1140 400 C1120 420 1112 455 1140 480 C1160 500 1185 495 1200 490 Z"/>
      <path class="garland__cluster" fill="url(#garland-cluster)"
        d="M0 230 C40 210 110 215 135 250 C150 275 130 305 100 320 C80 340 50 355 20 350 C8 348 0 344 0 340 Z"/>
      <path class="garland__base" fill="url(#garland-base)"
        d="M0 360 C30 355 70 370 90 400 C120 440 170 470 230 500 C300 530 380 535 450 545 C520 555 580 570 620 600 L630 617 H0 Z"/>
    </svg>

    <p class="invitation__text hosts">Margaret &amp; David Hollis</p>
    <p class="invitation__text invite-line">invite you to celebrate the engagement of</p>
    <h1 class="invitation__text couple">Marnie &amp; Thomas</h1>
    <p class="invitation__text event-date">Saturday 23 January 2021, 6.30pm</p>
    <p class="invitation__text event-address">41 Ridge Street, Laurel Bay</p>
  </main>
</body>
</html>
```